$5 Quest Website Required

I am looking for someone to develop a website akin to the simplicity of www.boxlantern.example with a video in the center or a tab that permits one to "Accept the Challenge."

Incorporates our logo and is used to promote our "$5 Quest Program."

Please see attachments, but we are igniting entrepreneurial spirit among our nation's youth through this interactive and intensive program!

There should be a way to navigate to other sections of the site including:

About
Why
Request $5 Quest Packet
Success Stories
Partners
Link to Norvik Holdings
Updates

Thanks to all in advance!

Looking forward to working with you!

Good feel of what we are looking for in terms of "feel"

http://www.thebrightripple.example/

Thank you,

RB

Please make note of this website, we are going for a feel that is akin to this and less modern and professional...more abstract and interactive...but of course include space for our video:

Colors, feel, imagery, is great. Keep your formats, but bring on the feel!

Thank you all for your hard work and patience.

Thank you all for your hard work thus far.

Meanwhile, please understand that the $5 Quest is young, youthful, full of challenge and vitality, it is a competition among students from high school and universities.  The websites you have delivered are too corporate, stale, and standard.  I'm looking for something that is fresh, different, like www.thebrightripple.example.

Symbols, cartoonish, but serious, down to business and save the world one $5 bill at a time.  The logo can be used as a theme...the colors, the feel.

Video space for explanation on the $5 Quest front and center.  With leaves, $ signs, colorful colors, etc.

Visual needs to be compelling to Join the Challenge! Although Norvik Holdings and the tree is a parent company; $5 Quest is separate and Norvik Holdings should only be mentioned as a link.

PixelHarbor.example in regard to simplicity; and www.thebrightripple.example in terms of style.

Thank you,

Raphael

Like the designs that have been submitted; we are almost there.

Target Market(s)

Professors, students, teachers, parents and NGO leaders who wish to use our program as a way to inspire leadership/entrepreneurship/fundraise for their causes.

Requirements
Must have
• Place for the video, front and center
Include logo
Forsight for blogging, message, etc.
Nice to have
• Plan "buckets" to include"
Explanation Video
Two pamphlets
Contract
FAQs
Website with Blog, voting, registration, video upload, etc.
Flyer perfected
Parable...symbol of our life
Photos
Stats included
Testimonials
Organizations that have used (TKWLM, North Brook Lodge, Marlowton High)
Sponsors (Open Lantern, Copperleaf Learningfield)
Photos from events

I understand this takes coding and such, but want you to be aware of the long term vision for it!

```html
<!DOCTYPE html>
<html lang="en">
<head>
<meta charset="utf-8">
<title>$5 Quest</title>
<link rel="stylesheet" href="https://fonts.googleapis.com/css2?family=Roboto+Condensed:wght@400;700&family=Noto+Sans:wght@400&family=Arimo:wght@400&display=swap">
<style>
  :root {
    --green: #0d9345;
    --green-dark: #0a7a39;
    --orange: #f7941d;
    --ink: #4b4b4e;
    --text: #555555;
    --rule-yellow: #f3d23a;
    --paper: #fdf8e9;
    --paper-deep: #f4ead0;
    --frame: #dcdcdc;
    --white: #ffffff;
  }
  * { margin: 0; padding: 0; box-sizing: border-box; }
  html, body { width: 1200px; height: 989px; overflow: hidden; }
  body {
    position: relative;
    background: var(--paper);
    font-family: "Noto Sans", sans-serif;
    color: var(--text);
  }
  .backdrop {
    position: absolute; inset: 0;
    background:
      radial-gradient(ellipse 420px 260px at 600px 110px, rgba(255,255,255,0.9), rgba(255,255,255,0) 70%),
      linear-gradient(180deg, var(--paper) 0%, var(--paper-deep) 55%, var(--paper) 100%);
  }
  .utility {
    position: absolute; top: 0; right: 34px; height: 28px;
    display: flex; align-items: center;
    font-family: "Roboto Condensed", sans-serif; font-size: 16px; color: #222;
  }
  .utility a { color: inherit; text-decoration: none; padding: 0 12px; letter-spacing: .5px; }
  .utility .signin { background: #ececec; height: 28px; line-height: 28px; }
  .utility .language {
    background: var(--green); color: var(--white); height: 28px; line-height: 28px;
    font-size: 14px; font-weight: 700; padding: 0 10px; border-radius: 0 0 3px 3px;
    display: flex; align-items: center; gap: 14px; margin-left: 6px;
  }
  .brand {
    position: absolute; top: 56px; left: 0; width: 1200px;
    display: flex; justify-content: center; align-items: center; gap: 22px;
  }
  .brand-mark { width: 110px; height: 110px; border-radius: 50%; background: var(--green); }
  .brand-name {
    font-family: "Noto Sans", sans-serif; font-size: 82px; color: var(--ink); letter-spacing: 1px;
  }
  .main-nav {
    position: absolute; top: 232px; left: 0; width: 1200px;
    display: flex; justify-content: center; align-items: center;
    font-family: "Roboto Condensed", sans-serif; font-size: 22px; color: var(--ink); letter-spacing: .5px;
  }
  .main-nav a { color: inherit; text-decoration: none; }
  .main-nav a.current { color: var(--green); }
  .main-nav .dot { width: 6px; height: 6px; border-radius: 50%; background: var(--green); margin: 0 22px; }
  .nav-rule { position: absolute; top: 276px; left: 24px; width: 1152px; height: 1px; background: var(--rule-yellow); }

  .welcome { position: absolute; top: 328px; left: 24px; width: 316px; }
  .section-title { font-size: 21px; font-weight: 400; line-height: 28px; }
  .welcome .section-title { color: var(--orange); }
  .welcome .section-title span { color: var(--green); }
  .dotted { border-bottom: 1px dotted #444; margin-top: 8px; }
  .welcome p, .testimonial p {
    font-size: 14.5px; line-height: 21.6px; text-align: justify; color: var(--text);
  }
  .welcome .dotted { margin-bottom: 18px; }
  .welcome p + p { margin-top: 8px; }

  .video-frame {
    position: absolute; top: 298px; left: 395px; width: 531px; height: 445px;
    border: 1px solid #f3c94b; border-radius: 10px; background: var(--white);
    box-shadow: 0 14px 16px -10px rgba(0,0,0,0.25);
  }
  .video-screen {
    position: absolute; top: 7px; left: 7px; right: 4px; bottom: 5px;
    border: 7px solid var(--frame); border-radius: 6px; background: var(--white);
  }
  .video-label {
    position: absolute; top: 606px; left: 395px; width: 531px; text-align: center;
    font-family: "Roboto Condensed", sans-serif; font-size: 32px; color: #222; letter-spacing: .5px;
  }
  .play-button { position: absolute; top: 397px; left: 573px; }

  .testimonials { position: absolute; top: 328px; left: 976px; width: 200px; }
  .testimonials .section-title { color: var(--green); text-align: right; padding-right: 6px; }
  .testimonials .section-title span { color: var(--orange); }
  .testimonials .dotted { margin-top: 10px; }
  .testimonial { position: absolute; left: 6px; width: 170px; }
  .testimonial cite {
    position: absolute; right: -28px; font-style: normal; font-size: 14.5px; color: var(--text); white-space: nowrap;
  }
  .testimonial.one { top: 70px; }
  .testimonial.one cite { top: 102px; }
  .testimonial.two { top: 224px; left: 3px; }
  .testimonial.two cite { top: 103px; }

  .cta-line { position: absolute; top: 820px; height: 0; border-top: 2px dashed var(--green); }
  .cta-line.left { left: 302px; width: 160px; }
  .cta-line.right { left: 828px; width: 156px; }
  .cta { position: absolute; top: 788px; left: 444px; }
  .cta-text {
    position: absolute; top: 788px; left: 444px; width: 398px; height: 65px;
    display: flex; align-items: center; justify-content: center;
    font-family: "Roboto Condensed", sans-serif; font-size: 26px; color: var(--white); letter-spacing: .3px;
  }

  .footer-rule { position: absolute; top: 902px; left: 24px; width: 1152px; border-top: 2px dotted #cfcfcf; }
  .footer-brand { position: absolute; top: 926px; left: 40px; display: flex; align-items: center; gap: 8px; }
  .footer-brand .brand-mark { width: 34px; height: 34px; }
  .footer-brand .brand-name { font-size: 24px; }
  .footer-nav {
    position: absolute; top: 925px; right: 40px; display: flex; gap: 19px;
    font-family: "Arimo", sans-serif; font-size: 13px; color: #222;
  }
  .footer-nav a { color: inherit; text-decoration: none; }
  .copyright {
    position: absolute; top: 952px; right: 40px;
    font-family: "Arimo", sans-serif; font-size: 13px; color: #222;
  }
</style>
</head>
<body>
  <div class="backdrop" role="img" aria-label="Soft cream background with light rays and faint stacks of banknotes"></div>

  <nav class="utility">
    <a href="#">FAQ</a>
    <a href="#" class="signin">SIGNIN</a>
    <span class="language">LANGUAGE
      <svg width="12" height="10" viewBox="0 0 12 10"><path d="M0 0h12L6 10z" fill="#fff"/></svg>
    </span>
  </nav>

  <header class="brand">
    <span class="brand-mark"></span>
    <span class="brand-name">$5 Quest</span>
  </header>

  <nav class="main-nav">
    <a href="#" class="current">HOME</a><span class="dot"></span>
    <a href="#">ABOUT US</a><span class="dot"></span>
    <a href="#">WHY WE ARE?</a><span class="dot"></span>
    <a href="#">SUCCESS STORIES</a><span class="dot"></span>
    <a href="#">PARTNERS</a><span class="dot"></span>
    <a href="#">NORVIK HOLDINGS</a>
  </nav>
  <div class="nav-rule"></div>

  <section class="welcome">
    <h2 class="section-title">WELCOME TO <span>$5 QUEST</span></h2>
    <div class="dotted"></div>
    <p>Lorem ipsum dolor sit amet, consectetur adipiscing elit. Curabitur eu nisl odio. Cras egestas turpis in mi feugiat vel tincidunt arcu accumsan. Phasellus non posuere eros. Aenean consectetur.</p>
    <p>sapien in elit luctus ac posuere purus placerat. Aliquam turpis lorem,.</p>
    <p>Donec fermentum sodales erat, quis consequat nisi ornare eget. Duis volutpat justo ut ante imperdiet feugiat. &nbsp;fermentum sodales erat, quis consequat nisi ornare eget. Duis volutpat justo ut ante imperdiet feugiat.</p>
    <p>sapien in elit luctus ac posuere purus placerat. Aliquam turpis lorem,.</p>
  </section>

  <div class="video-frame"><div class="video-screen"></div></div>
  <svg class="play-button" width="174" height="174" viewBox="0 0 174 174" aria-label="Play video">
    <defs>
      <linearGradient id="playFill" x1="0" y1="0" x2="0" y2="1">
        <stop offset="0" stop-color="#3a3a3a"/>
        <stop offset="1" stop-color="#0c0c0c"/>
      </linearGradient>
    </defs>
    <circle cx="87" cy="87" r="87" fill="url(#playFill)"/>
    <path d="M70 52 L118 87 L70 122 Z" fill="#e3e3e3"/>
  </svg>
  <div class="video-label">WATCH VIDEO</div>

  <aside class="testimonials">
    <h2 class="section-title">Client <span>Testimonials</span></h2>
    <div class="dotted"></div>
    <div class="testimonial one">
      <p>Lorem ipsum dolor sit amsectetur adipiscing elit. Curabitur eu nisl odio. dolor sit amsectetur u nisl odio.</p>
      <cite>- LOREM IPSUM</cite>
    </div>
    <div class="testimonial two">
      <p>Lorem ipsum dolor sit amsectetur adipiscing elit. Curabitur eu nisl odio. dolor sit amsectetur u nisl odio.</p>
      <cite>- LOREM IPSUM</cite>
    </div>
  </aside>

  <div class="cta-line left"></div>
  <div class="cta-line right"></div>
  <svg class="cta" width="398" height="65" viewBox="0 0 398 65">
    <path d="M0 0 H398 L383 32.5 L398 65 H0 L15 32.5 Z" fill="var(--green)"/>
  </svg>
  <a class="cta-text" href="#" style="text-decoration:none">ACCEPT THE QUEST</a>

  <div class="footer-rule"></div>
  <div class="footer-brand">
    <span class="brand-mark"></span>
    <span class="brand-name">$5 Quest</span>
  </div>
  <nav class="footer-nav">
    <a href="#">Home</a>
    <a href="#">About Us</a>
    <a href="#">Success Stories</a>
    <a href="#">Partners</a>
    <a href="#">Norvik Holdings</a>
    <a href="#">Terms</a>
    <a href="#">Privacy Policy</a>
  </nav>
  <p class="copyright">All Rights reserved @ $5quest</p>
</body>
</html>
```